MBRDC redesign and update stationary bc envelopes.

Stationary, Envelopes, Brochures, Business Card. Need to add second surgeon and two other offices. I need everything to match. I am a oral & maxillofacial surgeon.
Additional surgeon and three office addresses.
Jae Min Park, DMD, MD, INC

3718 Silver Meadow Parkway
Cedar Ridge, CA 95741

642 Lorin Way, Suite 101
Brookdale, CA. 95628

2317 Vale Street, Suite 105
Pine Hollow, CA. 95614
Updates

Logo design uploaded. Zapfino Extra/Adobe Garamond/Palatino are fonts used before. Not sure what is on exisiting stationary.

Target Market(s)

Referral dentist and sometimes patients. I am a oral & Maxillofacial surgeon.

Industry/Entity Type

Dental Clinic

Font styles to use
Serif
Script

Requirements
Must have
• Color of existing stationary. Update is possible.
Nice to have
• Conservative/modern
Should not have
• Playful

```html
<!DOCTYPE html>
<html lang="en">
<head>
<meta charset="utf-8">
<title>MBRDC Stationery</title>
<link rel="stylesheet" href="https://fonts.googleapis.com/css2?family=EB+Garamond&family=Open+Sans&family=Arimo&display=swap">
<style>
:root{
  --bg:#e4e4e4;
  --paper:#ffffff;
  --green:#6b8e23;
  --ink:#1e1e1e;
  --body:#555555;
  --hill-a:#f7f1c8;
  --hill-b:#fbf8e6;
  --rule:#9a9a9a;
}
*{margin:0;padding:0;box-sizing:border-box}
html,body{width:1200px;height:769px;overflow:hidden;background:var(--bg)}
.canvas{position:relative;width:1200px;height:769px}
.sheet{position:absolute;background:var(--paper);box-shadow:0 1px 4px rgba(0,0,0,.25);overflow:hidden}
.abs{position:absolute;white-space:nowrap}
.serif{font-family:"EB Garamond",Georgia,serif;color:var(--green)}
.sans{font-family:"Arimo",Arial,sans-serif;color:var(--ink)}
.body{font-family:"Open Sans",Helvetica,sans-serif;color:var(--body)}
.hills{position:absolute;left:0;right:0;bottom:0;background:linear-gradient(to top,var(--hill-a),var(--hill-b) 60%,rgba(255,255,255,0));}
.brand{display:flex;align-items:center;gap:5px;font-family:"EB Garamond",Georgia,serif;color:var(--green)}
.brand-dot{border-radius:50%;background:var(--green)}
.vrule{position:absolute;width:1px;background:var(--rule)}
.ico{display:inline-block;vertical-align:-1px;margin-right:3px}
/* letterhead */
.letterhead{left:87px;top:100px;width:437px;height:560px}
.letterhead .para{position:absolute;left:41px;width:354px;font-size:7px;line-height:12.6px;text-align:justify}
/* envelope */
.envelope{left:597px;top:171px;width:508px;height:229px}
/* card */
.card{left:771px;top:466px;width:233px;height:139px}
</style>
</head>
<body>
<div class="canvas">

  <!-- Letterhead -->
  <section class="sheet letterhead">
    <div class="hills" style="height:105px;border-radius:60% 60% 0 0/40% 40% 0 0" role="img" aria-label="Soft illustration of golden rolling foothills"></div>

    <div class="brand abs" style="left:45px;top:42px;font-size:20px">
      <span class="brand-dot" style="width:12px;height:12px"></span>MBRDC
    </div>

    <div class="vrule" style="left:257px;top:15px;height:68px"></div>
    <div class="abs serif" style="left:267px;top:14px;font-size:8px;line-height:10px">Martin K. Hale, DDS, INC<br>Jae Min Park, DMD, MD, INC</div>
    <div class="abs sans" style="left:267px;top:35px;font-size:6px;line-height:8px">Diplomates of the American Board of<br>Oral &amp; Maxillofacial Surgery<br>Dental Implants and Oral Surgery</div>
    <div class="abs sans" style="left:267px;top:62px;font-size:6px;line-height:8.2px">
      <span class="ico"><svg width="6" height="6" viewBox="0 0 10 10"><path d="M2 1l2 2-1 1.5c.8 1.5 1.8 2.5 3.5 3.5L8 7l2 2-1.5 1C4 9.5.5 6 1 1z" fill="var(--green)"/></svg></span>916.555.0142
      <span class="ico" style="margin-left:3px"><svg width="6" height="6" viewBox="0 0 10 10"><rect x="1" y="4" width="8" height="4" fill="var(--green)"/><rect x="3" y="1" width="4" height="3" fill="var(--green)"/></svg></span>916.555.0187<br>
      <span class="ico"><svg width="6" height="5" viewBox="0 0 10 8"><rect width="10" height="8" fill="var(--green)"/><path d="M0 0l5 4 5-4" stroke="#fff" fill="none"/></svg></span>drhale@meadowbrookoralsurgery.com<br>
      <span class="ico"><svg width="6" height="6" viewBox="0 0 10 10"><circle cx="5" cy="5" r="4.3" fill="none" stroke="var(--green)" stroke-width="1.2"/><path d="M1 5h8M5 1v8" stroke="var(--green)"/></svg></span>www.meadowbrookoralsurgery.com
    </div>

    <div class="abs body" style="left:41px;top:102px;font-size:6.8px">Issuing Date: May 5, 2018</div>
    <div class="abs body" style="left:41px;top:118px;font-size:6.8px;line-height:8.4px">Name Of Employee Mr. XYZABC<br>Address of Employee<br>Address Line 2 etc..</div>
    <div class="abs body" style="left:41px;top:167px;font-size:6.8px">Dear Mr.XYZABC</div>

    <p class="para body" style="top:189px">Lorem Ipsum has been the industry's standard dummy text ever since the 1500s, when an unknown printer took a galley of type and scrambled it to make a type specimen book. It has survived not only five centuries, but also the leap into electronic typesetting, remaining essentially unchanged. It was popularised in the 1960s with the release of Letraset sheets containing Lorem Ipsum passages, and more recently with desktop publishing software like Aldus PageMaker including versions of Lorem Ipsum.</p>
    <p class="para body" style="top:265px">Lorem Ipsum is simply dummy text of the printing and typesetting industry. Lorem Ipsum has been the industry's standard dummy text ever since the 1500s, when an unknown printer took a galley of type and scrambled it to make a type specimen book.</p>
    <p class="para body" style="top:315px">It has survived not only five centuries, but also the leap into electronic typesetting, remaining essentially unchanged. It was popularised in the 1960s with the release of Letraset sheets containing Lorem IpsumIpsum passages.</p>

    <div class="abs body" style="left:41px;top:380px;font-size:6.8px">Yours Sincerely</div>
    <div class="abs" style="left:41px;top:397px;width:100px;height:12px;background:linear-gradient(90deg,#e9e9e9,#f6f6f6)" role="img" aria-label="Handwritten signature"></div>
    <div class="abs body" style="left:41px;top:416px;font-size:8.5px;color:#333">Daniel Reyes</div>
    <div class="abs body" style="left:41px;top:431px;font-size:6.8px">Managing Director</div>

    <svg class="abs" style="left:51px;top:508px" width="336" height="16" viewBox="0 0 336 16">
      <line x1="0" y1="12" x2="160" y2="12" stroke="#666" stroke-width=".6"/>
      <line x1="176" y1="12" x2="336" y2="12" stroke="#666" stroke-width=".6"/>
      <path d="M168 1a4.5 4.5 0 0 1 4.5 4.5c0 3.5-4.5 9-4.5 9s-4.5-5.5-4.5-9A4.5 4.5 0 0 1 168 1z" fill="var(--green)"/>
      <circle cx="168" cy="5.5" r="1.6" fill="#fff"/>
    </svg>
    <div class="vrule" style="left:169px;top:526px;height:20px;background:#777"></div>
    <div class="vrule" style="left:277px;top:526px;height:20px;background:#777"></div>
    <div class="abs sans" style="left:54px;top:528px;width:108px;text-align:center;font-size:7.5px;line-height:9.5px">3718 Silver Meadow Parkway<br>Cedar Ridge, CA 95741</div>
    <div class="abs sans" style="left:172px;top:528px;width:103px;text-align:center;font-size:7.5px;line-height:9.5px">642 Lorin Way, Suite 101<br>Brookdale, CA. 95628</div>
    <div class="abs sans" style="left:280px;top:528px;width:112px;text-align:center;font-size:7.5px;line-height:9.5px">2317 Vale Street, Suite 105<br>Pine Hollow, CA. 95614</div>
  </section>

  <!-- Envelope -->
  <section class="sheet envelope">
    <div class="hills" style="height:96px;border-radius:70% 30% 0 0/60% 40% 0 0" role="img" aria-label="Soft illustration of golden rolling foothills"></div>
    <div class="brand abs" style="left:16px;top:44px;font-size:15px">
      <span class="brand-dot" style="width:9px;height:9px"></span>MBRDC
    </div>
    <div class="vrule" style="left:94px;top:17px;height:80px"></div>
    <div class="abs serif" style="left:100px;top:16px;font-size:8px;line-height:10px">Martin K. Hale, DDS, INC<br>Jae Min Park, DMD, MD, INC</div>
    <div class="abs sans" style="left:100px;top:38px;font-size:6.3px;line-height:8.6px">Diplomates of the American Board of Oral &amp; Maxillofacial Surgery<br>Dental Implants and Oral Surgery</div>
    <div class="abs sans" style="left:100px;top:64px;font-size:6.3px;line-height:10.4px">
      <span class="ico"><svg width="4" height="6" viewBox="0 0 8 12"><path d="M4 0a4 4 0 0 1 4 4c0 3-4 8-4 8S0 7 0 4a4 4 0 0 1 4-4z" fill="var(--green)"/></svg></span>3718 Silver Meadow Parkway, Cedar Ridge, CA 95741<br>
      <span class="ico"><svg width="4" height="6" viewBox="0 0 8 12"><path d="M4 0a4 4 0 0 1 4 4c0 3-4 8-4 8S0 7 0 4a4 4 0 0 1 4-4z" fill="var(--green)"/></svg></span>642 Lorin Way, Suite 101 , Brookdale, CA. 95628<br>
      <span class="ico"><svg width="4" height="6" viewBox="0 0 8 12"><path d="M4 0a4 4 0 0 1 4 4c0 3-4 8-4 8S0 7 0 4a4 4 0 0 1 4-4z" fill="var(--green)"/></svg></span>2317 Vale Street, Suite 105, Pine Hollow, CA. 95614
    </div>
    <div class="abs serif" style="left:0;width:508px;top:204px;text-align:center;font-size:9.5px;letter-spacing:1.6px;padding-left:18px">www.meadowbrookoralsurgery.com</div>
  </section>

  <!-- Business card -->
  <section class="sheet card">
    <div class="hills" style="height:22px" role="img" aria-label="Soft illustration of golden rolling foothills"></div>
    <div class="abs serif" style="left:10px;top:12px;font-size:8.5px;line-height:10px">Martin K. Hale, DDS, INC<br>Jae Min Park, DMD, MD, INC</div>
    <div class="abs body" style="left:10px;top:34px;font-size:5.6px;line-height:8.5px;color:var(--ink)">Diplomates of the American Board of<br>Oral &amp; Maxillofacial Surgery<br>Dental Implants and Oral Surgery</div>
    <div class="abs body" style="left:10px;top:63px;font-size:5.8px;line-height:8.7px;color:var(--ink)">
      <span class="ico"><svg width="5" height="5" viewBox="0 0 10 10"><path d="M2 1l2 2-1 1.5c.8 1.5 1.8 2.5 3.5 3.5L8 7l2 2-1.5 1C4 9.5.5 6 1 1z" fill="var(--green)"/></svg></span>916.555.0142<br>
      <span class="ico"><svg width="5" height="5" viewBox="0 0 10 10"><rect x="1" y="4" width="8" height="4" fill="var(--green)"/><rect x="3" y="1" width="4" height="3" fill="var(--green)"/></svg></span>916.555.0187<br>
      <span class="ico"><svg width="5" height="4" viewBox="0 0 10 8"><rect width="10" height="8" fill="var(--green)"/><path d="M0 0l5 4 5-4" stroke="#fff" fill="none"/></svg></span>drhale@meadowbrookoralsurgery.com
    </div>
    <div class="abs serif" style="left:10px;top:92px;font-size:6.2px;letter-spacing:.9px">www.meadowbrookoralsurgery.com</div>
    <div class="abs body" style="left:10px;top:104px;font-size:5.6px;line-height:8.3px;color:var(--ink)">
      <span class="ico"><svg width="4" height="5" viewBox="0 0 8 12"><path d="M4 0a4 4 0 0 1 4 4c0 3-4 8-4 8S0 7 0 4a4 4 0 0 1 4-4z" fill="var(--green)"/></svg></span>3718 Silver Meadow Parkway Cedar Ridge, CA 95741<br>
      <span class="ico"><svg width="4" height="5" viewBox="0 0 8 12"><path d="M4 0a4 4 0 0 1 4 4c0 3-4 8-4 8S0 7 0 4a4 4 0 0 1 4-4z" fill="var(--green)"/></svg></span>2317 Vale Street, Suite 105 Pine Hollow, CA. 95614<br>
      <span class="ico"><svg width="4" height="5" viewBox="0 0 8 12"><path d="M4 0a4 4 0 0 1 4 4c0 3-4 8-4 8S0 7 0 4a4 4 0 0 1 4-4z" fill="var(--green)"/></svg></span>642 Lorin Way, Suite 101 Brookdale, CA. 95628
    </div>
    <div class="brand abs" style="left:135px;top:45px;font-size:18px">
      <span class="brand-dot" style="width:10px;height:10px"></span>MBRDC
    </div>
  </section>

</div>
</body>
</html>
```